My project benefits Military, First Responders, Police, Fire, and Educators.

Contact Information for Business Card

2 Sided appointment card. Visual side will have my head shot with "Brisk Lantern" in a bold graffic/text. I am picturing maybe the headshot applied to a filter that has a matrix effect where the picture is made up of data/numbers flowing vertically through the photo. I am of course open to other concepts as well. Side two will have contact info presented in an attractive visual complimenting the front.

```html
<!DOCTYPE html>
<html lang="en">
<head>
<meta charset="utf-8">
<title>Brisk Lantern – Appointment Card</title>
<link href="https://fonts.googleapis.com/css2?family=Oswald:wght@700&family=Source+Sans+3:wght@400;600&display=swap" rel="stylesheet">
<style>
  :root {
    --backdrop-top: #262626;
    --backdrop-bottom: #050505;
    --card-white: #ffffff;
    --band-dark: #242424;
    --ink: #222222;
    --ink-light: #e8e8e8;
    --rule: #8a8a8a;
    --photo-light: #f2f0ec;
    --photo-mid: #b99a86;
    --photo-dark: #1f2438;
  }
  * { margin: 0; padding: 0; box-sizing: border-box; }
  html, body { width: 1200px; height: 900px; overflow: hidden; }
  body {
    position: relative;
    background: linear-gradient(180deg, var(--backdrop-top) 0%, var(--backdrop-bottom) 100%);
    font-family: "Source Sans 3", "Myriad Pro", Arial, sans-serif;
  }
  .card {
    position: absolute;
    top: 170px;
    width: 347px;
    height: 560px;
    background: var(--card-white);
    overflow: hidden;
  }
  .card--front { left: 259px; }
  .card--back { left: 631px; }

  .headshot {
    position: absolute;
    left: 0; top: 0;
    width: 347px; height: 340px;
    background:
      radial-gradient(ellipse 90px 120px at 50% 38%, var(--photo-mid) 0%, rgba(185,154,134,0) 100%),
      linear-gradient(180deg, var(--photo-light) 0%, var(--photo-light) 62%, var(--photo-dark) 100%);
  }
  .contact-band {
    position: absolute;
    left: 0; top: 340px;
    width: 347px; height: 220px;
    background: var(--band-dark);
    color: var(--ink-light);
    text-align: center;
  }
  .contact-band__name {
    position: absolute; left: 0; right: 0; top: 60px;
    font-size: 22px; font-weight: 600; letter-spacing: 0.2px;
  }
  .contact-band__role {
    position: absolute; left: 0; right: 0; top: 88px;
    font-size: 14.5px;
  }
  .contact-band__list {
    position: absolute; left: 0; right: 0; top: 121px;
    list-style: none;
    font-size: 14.5px; line-height: 21px;
  }
  .contact-band__list b { font-weight: 600; }

  .brand-mark {
    position: absolute;
    left: 126px; top: 49px;
    width: 96px; height: 96px;
    border-radius: 50%;
    background: var(--ink);
  }
  .brand-name {
    position: absolute; left: 0; right: 0; top: 154px;
    text-align: center;
    font-family: "Oswald", "Impact", sans-serif;
    font-weight: 700;
    font-size: 44px;
    line-height: 1;
    color: var(--ink);
    letter-spacing: 0.3px;
  }
  .appointment {
    position: absolute; left: 0; right: 0; top: 318px;
    text-align: center; color: var(--ink);
  }
  .appointment__lead { font-size: 21px; line-height: 26px; word-spacing: 3px; }
  .appointment__title { font-size: 34px; line-height: 40px; margin-top: 4px; }
  .appointment__line {
    position: absolute; left: 28px; width: 291px; height: 1px;
    background: var(--rule);
  }
  .appointment__line--one { top: 425px; }
  .appointment__line--two { top: 461px; }
  .appointment__note {
    position: absolute; left: 0; right: 0; top: 490px;
    text-align: center; color: var(--ink);
    font-size: 13.5px; line-height: 18px;
  }
</style>
</head>
<body>
  <section class="card card--front">
    <div class="headshot" role="img" aria-label="Head-and-shoulders portrait of the managing director in a dark suit, shirt and tie"></div>
    <div class="contact-band">
      <p class="contact-band__name">MARCUS HALE</p>
      <p class="contact-band__role">Managing Director</p>
      <ul class="contact-band__list">
        <li><b>P:</b> 823-555-0142</li>
        <li><b>E:</b> hello@brisklantern.com</li>
        <li><b>W::</b> www.brisklantern.com</li>
      </ul>
    </div>
  </section>

  <section class="card card--back">
    <div class="brand-mark" aria-hidden="true"></div>
    <p class="brand-name">BRISK LANTERN</p>
    <div class="appointment">
      <p class="appointment__lead">Your Next</p>
      <p class="appointment__title">Appointment :</p>
    </div>
    <div class="appointment__line appointment__line--one"></div>
    <div class="appointment__line appointment__line--two"></div>
    <p class="appointment__note">Please give 24 hours notice if you need<br>to reschedule your appointment</p>
  </section>
</body>
</html>
```